New Business Card Design Project

Use the flyer uploaded and website www.brightoakbuilders.com for inspiration.
List Our Services on Backside of business cards
Marcus Delling
Harborline Builders Inc.
Licensed General Contractors
858-471-6093

Contact Information for Business Card

Use the flyer uploaded and website www.brightoakbuilders.com for inspiration. List Our Services on Backside of business cards Marcus Delling Harborline Builders Inc. Licensed General Contractors 858-471-6093

```html
<!DOCTYPE html>
<html lang="en">
<head>
<meta charset="utf-8">
<title>Harborline Builders Inc. – Business Card</title>
<link rel="stylesheet" href="https://fonts.googleapis.com/css2?family=Montserrat:wght@400;500;700;800&display=swap">
<style>
  :root{
    --bg:#2b2b2b;
    --card:#111111;
    --ink:#ffffff;
    --ink-soft:#e6e6e6;
  }
  *{box-sizing:border-box;margin:0;padding:0}
  html,body{width:1200px;height:998px;overflow:hidden;background:var(--bg)}
  body{position:relative;font-family:"Montserrat",sans-serif;color:var(--ink)}
  .card{position:absolute;width:620px;height:354px;background:var(--card);box-shadow:0 12px 30px rgba(0,0,0,.55);overflow:hidden}
  .card--back{left:60px;top:60px}
  .card--front{left:520px;top:584px}

  .brand{display:flex;align-items:center;gap:12px}
  .brand-mark{width:14px;height:14px;border:2px solid var(--ink);flex:none}
  .brand-name{font-weight:500;letter-spacing:.1em;text-transform:uppercase;color:var(--ink);font-size:20px;line-height:1;white-space:nowrap}

  /* back */
  .card--back .brand{position:absolute;left:0;right:0;top:86px;justify-content:center}
  .services-title{position:absolute;left:40px;right:40px;top:150px;display:flex;align-items:center;gap:14px}
  .services-title::before,.services-title::after{content:"";flex:1;height:2px;background:var(--ink)}
  .services-title span{font-weight:800;font-size:17px;letter-spacing:.04em}
  .services{position:absolute;top:190px;left:40px;right:30px;display:grid;grid-template-columns:1fr 1fr;column-gap:20px}
  .services ul{list-style:none}
  .services li{display:flex;align-items:center;gap:8px;font-size:14.5px;line-height:1.55;font-weight:400;white-space:nowrap}
  .tick{width:14px;height:14px;flex:none}

  /* front */
  .card--front .brand{position:absolute;left:60px;top:96px}
  .contact-name{position:absolute;left:60px;top:160px;font-weight:700;font-size:30px;line-height:1.2}
  .contact-role{position:absolute;left:60px;top:205px;font-weight:700;font-size:15px}
  .contact-rule{position:absolute;left:60px;top:236px;width:260px;height:2px;background:var(--ink)}
  .contact-list{position:absolute;left:60px;top:254px;list-style:none}
  .contact-list li{display:flex;align-items:center;gap:12px;font-size:16px;line-height:1.9}
  .icon{width:16px;height:16px;flex:none}
</style>
</head>
<body>

<section class="card card--back" aria-label="Card back – services">
  <div class="brand">
    <span class="brand-mark" aria-hidden="true"></span>
    <span class="brand-name">Harborline Builders Inc.</span>
  </div>
  <h2 class="services-title"><span>OUR SERVICES</span></h2>
  <div class="services">
    <ul>
      <li><svg class="tick" viewBox="0 0 14 14"><rect x="1" y="1" width="12" height="12" fill="none" stroke="#fff" stroke-width="1.6"/><path d="M3.5 7l2.5 2.5 4.5-5" fill="none" stroke="#fff" stroke-width="1.8"/></svg>Remodel: Kithcen &amp; Bath</li>
      <li><svg class="tick" viewBox="0 0 14 14"><rect x="1" y="1" width="12" height="12" fill="none" stroke="#fff" stroke-width="1.6"/><path d="M3.5 7l2.5 2.5 4.5-5" fill="none" stroke="#fff" stroke-width="1.8"/></svg>Painting: Interior &amp; Exterior</li>
      <li><svg class="tick" viewBox="0 0 14 14"><rect x="1" y="1" width="12" height="12" fill="none" stroke="#fff" stroke-width="1.6"/><path d="M3.5 7l2.5 2.5 4.5-5" fill="none" stroke="#fff" stroke-width="1.8"/></svg>Flooring: Carpet, Vinyl, Wood</li>
      <li><svg class="tick" viewBox="0 0 14 14"><rect x="1" y="1" width="12" height="12" fill="none" stroke="#fff" stroke-width="1.6"/><path d="M3.5 7l2.5 2.5 4.5-5" fill="none" stroke="#fff" stroke-width="1.8"/></svg>Window &amp; Door Replacement</li>
    </ul>
    <ul>
      <li><svg class="tick" viewBox="0 0 14 14"><rect x="1" y="1" width="12" height="12" fill="none" stroke="#fff" stroke-width="1.6"/><path d="M3.5 7l2.5 2.5 4.5-5" fill="none" stroke="#fff" stroke-width="1.8"/></svg>Plumbing: Repairs &amp; Upgrades</li>
      <li><svg class="tick" viewBox="0 0 14 14"><rect x="1" y="1" width="12" height="12" fill="none" stroke="#fff" stroke-width="1.6"/><path d="M3.5 7l2.5 2.5 4.5-5" fill="none" stroke="#fff" stroke-width="1.8"/></svg>Energy- Efficient Upgrades</li>
      <li><svg class="tick" viewBox="0 0 14 14"><rect x="1" y="1" width="12" height="12" fill="none" stroke="#fff" stroke-width="1.6"/><path d="M3.5 7l2.5 2.5 4.5-5" fill="none" stroke="#fff" stroke-width="1.8"/></svg>Deck &amp; Patio Construction</li>
    </ul>
  </div>
</section>

<section class="card card--front" aria-label="Card front – contact">
  <div class="brand">
    <span class="brand-mark" aria-hidden="true"></span>
    <span class="brand-name">Harborline Builders Inc.</span>
  </div>
  <h1 class="contact-name">Marcus Delling</h1>
  <p class="contact-role">Licensed General Contractors</p>
  <div class="contact-rule"></div>
  <ul class="contact-list">
    <li><svg class="icon" viewBox="0 0 16 16"><path d="M4 1.5l2.5 3-1.5 1.8a9 9 0 0 0 4.7 4.7l1.8-1.5 3 2.5-1.5 2.3C8 14.5 1.5 8 1.7 3z" fill="#fff"/></svg>858-471-6093</li>
    <li><svg class="icon" viewBox="0 0 16 16" fill="none" stroke="#fff" stroke-width="1.4"><circle cx="8" cy="8" r="6.5"/><ellipse cx="8" cy="8" rx="3" ry="6.5"/><path d="M1.5 8h13M2.5 4.8h11M2.5 11.2h11"/></svg>www.brightoakbuilders.com</li>
  </ul>
</section>

</body>
</html>
```